Webdesign für industrielle Produktion von Suppen, Saucen, Bouillons und Konzentraten
Zielgruppe
Industrielle Produktion von Suppen, Saucen, Bouillons und Konzentraten
Aufgabenstellung
Aufmachung nicht zu modern, eher klassisch Understatement

```html
<!DOCTYPE html>
<html lang="de">
<head>
<meta charset="utf-8">
<title>Veltro Foodservice – Kontakt</title>
<link href="https://fonts.googleapis.com/css2?family=Urbanist:wght@400;500;600;700;800&display=swap" rel="stylesheet">
<style>
:root{
  --red:#c8161d;
  --red-dark:#8e0c10;
  --red-deep:#6e0a0d;
  --ink:#111111;
  --muted:#333;
  --field:#efefef;
  --white:#ffffff;
  --map-base:#efe9dc;
}
*{box-sizing:border-box;margin:0;padding:0}
html,body{width:1200px;height:2368px;overflow:hidden}
body{position:relative;font-family:"Urbanist",sans-serif;color:var(--ink);background:var(--white)}
.abs{position:absolute}

/* hero */
.hero{left:0;top:0;width:1200px;height:413px;background:radial-gradient(ellipse at 50% 40%,#c9161c 0%,#a40f14 55%,#7e0a0e 100%)}
.nav-ribbon{top:52px;width:40px;height:64px;background:#e6e6e6}
.nav-ribbon.left{left:60px;clip-path:polygon(0 0,100% 0,100% 100%,0 100%,45% 50%)}
.nav-ribbon.right{left:1100px;clip-path:polygon(0 0,100% 0,55% 50%,100% 100%,0 100%)}
.nav{left:86px;top:40px;width:1029px;height:68px;background:var(--white);display:flex;align-items:center;font-size:14.5px;font-weight:500}
.nav-links{position:absolute;left:13px;display:flex;gap:16px}
.nav-active{position:absolute;left:626px;color:var(--red);font-weight:600}
.brand-badge{left:488px;top:16px;width:224px;height:118px;border-radius:50%;background:var(--white);display:flex;align-items:center;justify-content:center}
.brand-badge span{font-size:40px;font-weight:800;color:var(--red);letter-spacing:1px}
.search{position:absolute;left:735px;width:212px;height:34px;border:1.5px solid #555;border-radius:5px;display:flex;align-items:center;padding:0 14px;justify-content:space-between;font-size:14.5px}
.nav-icons{position:absolute;left:964px;display:flex;gap:16px;align-items:center}
.hero-kicker{top:165px;width:1200px;text-align:center;color:var(--white);font-size:18px;font-weight:500}
.hero-title{top:195px;width:1200px;text-align:center;color:var(--white);font-size:60px;font-weight:700;line-height:80px}

/* contact info */
.info{width:370px;text-align:center;font-size:13.5px;font-weight:500;line-height:17px}
.info h3{font-size:22px;font-weight:500;margin:10px 0 6px}
.info .lbl{color:var(--red)}
.map-title{top:733px;width:1200px;text-align:center;font-size:42px;font-weight:700}
.map{left:0;top:834px;width:1200px;height:412px;background:linear-gradient(135deg,#ede6d6 0%,#f2ecdf 45%,#e4efe0 100%)}
.map-btn{top:1160px;width:46px;height:46px;background:var(--white);border-radius:4px;box-shadow:0 1px 4px rgba(0,0,0,.25);display:flex;align-items:center;justify-content:center;font-size:30px;font-weight:400}

/* form */
.form-kicker{left:60px;top:1320px;font-size:17px;font-weight:500}
.form-title{left:60px;top:1348px;font-size:44px;font-weight:700;line-height:49px}
.form-title em{font-style:normal;color:var(--red)}
.field{background:var(--field);border-radius:4px;font-size:14.5px;font-weight:500;padding:0 20px;display:flex;align-items:center;color:#222}
.field.msg{align-items:flex-start;padding-top:16px}
.submit{left:60px;top:1804px;width:623px;height:39px;border-radius:6px;background:linear-gradient(180deg,var(--red) 0%,var(--red-deep) 100%);color:var(--white);font-size:15px;font-weight:600;display:flex;align-items:center;justify-content:center}
.photo{left:699px;top:1321px;width:441px;height:522px;border-radius:8px;background:radial-gradient(circle at 35% 25%,#e8a23a 0%,#c9b79c 22%,#8f8d86 55%,#6f6d68 100%)}

/* footer */
.footer{left:0;top:1925px;width:1200px;height:443px;background:radial-gradient(ellipse at 40% 50%,#c8121a 0%,#a10d13 60%,#7a080c 100%)}
.foot-brand{left:62px;top:1990px;font-size:52px;font-weight:800;color:var(--white)}
.foot-brand small{display:block;font-size:15px;font-weight:600;margin-top:-6px;margin-left:44px}
.foot-text{left:60px;top:2092px;width:330px;color:var(--white);font-size:13.5px;font-weight:500;line-height:16.5px}
.pay{top:2181px;width:37px;height:25px;background:var(--white);border-radius:3px;font-size:8px;font-weight:700;color:#333;display:flex;align-items:center;justify-content:center}
.sub-title{left:609px;top:2004px;color:var(--white);font-size:19px;font-weight:500;line-height:22px}
.sub-input{left:819px;top:1996px;width:321px;height:41px;background:var(--white);border-radius:5px;overflow:hidden;display:flex;align-items:center;font-size:14.5px;font-weight:500;padding-left:27px}
.sub-btn{position:absolute;right:0;top:0;width:49px;height:41px;background:var(--red);display:flex;align-items:center;justify-content:center}
.col{top:2068px;color:var(--white)}
.col h4{font-size:19px;font-weight:500;margin-bottom:20px}
.col a{display:block;color:var(--white);text-decoration:none;font-size:14.5px;font-weight:500;line-height:28px}
.foot-line{left:60px;top:2279px;width:1080px;height:1px;background:rgba(255,255,255,.75)}
.social{left:60px;top:2308px;display:flex;gap:8px}
.social span{width:18px;height:18px;border-radius:50%;background:var(--white);color:var(--red);font-size:6px;font-weight:700;display:flex;align-items:center;justify-content:center}
.copy{left:860px;top:2310px;width:280px;text-align:right;color:var(--white);font-size:11px;font-weight:500}
.copy b{font-weight:700}
</style>
</head>
<body>

<!-- header / hero -->
<section class="abs hero" role="img" aria-label="Rotes Hintergrundfeld mit dezentem Gemüsemuster"></section>
<div class="abs nav-ribbon left"></div>
<div class="abs nav-ribbon right"></div>
<nav class="abs nav">
  <div class="nav-links"><span>Geschäft</span><span>GV-Produkte</span><span>Catering-Produkte</span><span>Nachricht</span></div>
  <span class="nav-active">Kontakt</span>
  <div class="search"><span>Hier Suchen</span>
    <svg width="18" height="18" viewBox="0 0 24 24" fill="none" stroke="#111" stroke-width="2"><circle cx="10" cy="10" r="7"/><path d="M15 15l6 6"/></svg>
  </div>
  <div class="nav-icons">
    <svg width="18" height="18" viewBox="0 0 24 24" fill="none" stroke="#111" stroke-width="2"><circle cx="12" cy="8" r="4"/><path d="M4 21c1-5 15-5 16 0"/></svg>
    <svg width="20" height="18" viewBox="0 0 24 22" fill="none" stroke="#111" stroke-width="2"><path d="M1 2h4l3 12h12l2-8H6"/><circle cx="9" cy="19" r="1.5"/><circle cx="18" cy="19" r="1.5"/></svg>
  </div>
</nav>
<div class="abs brand-badge"><span>Veltro</span></div>
<p class="abs hero-kicker">Kontakt</p>
<h1 class="abs hero-title">Ihr Industriepartner<br>Erwartet Ihre Anfrage</h1>

<!-- contact info -->
<div class="abs info" style="left:47px;top:490px">
  <svg width="80" height="80" viewBox="0 0 80 80" fill="none" stroke="#c8161d" stroke-width="3" stroke-linejoin="round"><path d="M14 6l12 14-7 8c4 11 13 20 24 25l8-7 14 12-7 10C36 66 12 42 6 15z"/><path d="M44 22a12 12 0 0 1 12 12M46 12a22 22 0 0 1 20 20M48 2a32 32 0 0 1 28 28"/></svg>
  <h3>Contact Us</h3>
  <p><span class="lbl">Phone</span> +49-(0)-2000-41260 / -83520</p>
  <p><span class="lbl">Fax</span> +49-(0)-2000-47731 / -62904</p>
</div>
<div class="abs info" style="left:412px;top:486px">
  <svg width="60" height="78" viewBox="0 0 60 78" fill="none" stroke="#c8161d" stroke-width="3"><path d="M30 75C10 50 3 38 3 28a27 27 0 0 1 54 0c0 10-7 22-27 47z"/><circle cx="30" cy="27" r="11"/></svg>
  <h3>Address</h3>
  <p>Brandt &amp; Co. GmbH &amp; Co. KG</p>
  <p>Lindenweg 12 – 18</p>
  <p>40210 Musterstadt, Germany</p>
</div>
<div class="abs info" style="left:780px;top:505px">
  <svg width="76" height="52" viewBox="0 0 76 52" fill="none" stroke="#c8161d" stroke-width="3"><rect x="2" y="2" width="72" height="48"/><path d="M2 2l36 28L74 2M2 50l26-24M74 50L48 26"/></svg>
  <h3>Email</h3>
  <p>Info@Veltro-Suppen.De</p>
  <p>Http://Www.Veltro-Suppen.De</p>
</div>

<h2 class="abs map-title">View On Map</h2>
<div class="abs map" role="img" aria-label="Stadtplan mit Standortmarkierungen"></div>
<div class="abs map-btn" style="left:1032px">+</div>
<div class="abs map-btn" style="left:1094px">−</div>

<!-- contact form -->
<p class="abs form-kicker">Kontaktieren Sie Uns</p>
<h2 class="abs form-title">Beginnen Sie <em>Das Gespräch</em><br>Mit Uns</h2>
<div class="abs field" style="left:60px;top:1466px;width:299px;height:44px">Name</div>
<div class="abs field" style="left:382px;top:1466px;width:299px;height:44px">Phone Number</div>
<div class="abs field" style="left:60px;top:1533px;width:299px;height:44px">Email</div>
<div class="abs field" style="left:382px;top:1533px;width:299px;height:44px">Address</div>
<div class="abs field msg" style="left:60px;top:1600px;width:621px;height:174px">Message</div>
<div class="abs submit">Sumbit</div>
<div class="abs photo" role="img" aria-label="Foto von drei Suppenschalen auf grauem Leinentuch"></div>

<!-- footer -->
<footer class="abs footer" role="img" aria-label="Rotes Hintergrundbild mit Gewürzen auf Löffeln"></footer>
<div class="abs foot-brand">Veltro<small>Foodservice</small></div>
<p class="abs foot-text">Lorem Ipsum Dolor Sit Amet Consectetur. Ut Nulla Pellentesque Turpis Viverra Id Amet Bibendum.</p>
<div class="abs pay" style="left:60px">Karte</div>
<div class="abs pay" style="left:112px">Giro</div>
<div class="abs pay" style="left:165px">Kredit</div>
<div class="abs pay" style="left:217px">Wallet</div>
<div class="abs pay" style="left:270px">Mobil</div>

<p class="abs sub-title">Abonnieren Sie<br>Unseren Neuen Brief</p>
<div class="abs sub-input">Enter Your Email
  <div class="sub-btn"><svg width="12" height="16" viewBox="0 0 12 16" fill="none" stroke="#fff" stroke-width="2"><path d="M3 2l6 6-6 6"/></svg></div>
</div>
<div class="abs col" style="left:609px"><h4>Company</h4><a>About Us</a><a>Work With Us</a><a>Blog &amp; News</a></div>
<div class="abs col" style="left:842px"><h4>Shop</h4><a>Collections</a><a>Blog Post</a><a>Wishlist</a></div>
<div class="abs col" style="left:1056px"><h4>Quick Link</h4><a>Shop</a><a>Products</a><a>Contact</a></div>

<div class="abs foot-line"></div>
<div class="abs social"><span>Netz</span><span>Foto</span><span>Post</span><span>Feed</span></div>
<p class="abs copy">Copyright © 2024 <b>NORDFELD STUDIO</b>. All Rights Reserved.</p>

</body>
</html>
```